Dental Practice Website design

Design a new website for Brambleford Dental Practice.
Design should be warm, neutral in colour, with some small amount of bright colour if needed but kept to a minimum. Website should look professional, high end. Home page should be easy to navigate and simple for patients to be able to book online.
Logo in files along with some examples of websites that we like. Please ask if any further info needed.
Menu should have:
About
New Patients
Treatments
Fees
Contact Us

Industry/Entity Type

Dentistry

Number of Pages Required

4 page

Font styles to use
Sans Serif

Colors

Designer to choose colors to be used in the design.

Requirements
Must have
• Ravelle ratings badge, book online button,
Nice to have
• neutral, relaxing colours
Should not have
• harsh, bright colours!

```html
<!DOCTYPE html>
<html lang="en">
<head>
<meta charset="utf-8">
<title>Brambleford Dental Practice</title>
<link rel="stylesheet" href="https://fonts.googleapis.com/css2?family=Jost:wght@300;400;500;600&family=Plus+Jakarta+Sans:wght@500;600;700&display=swap">
<style>
:root{
  --ink:#1e2a2c;
  --ink-soft:#3a3a3a;
  --muted:#6d6d6d;
  --tan:#a8998a;
  --tan-band:#a3937f;
  --tan-text:#a8998a;
  --white:#ffffff;
  --light:#f4f4f3;
  --line:#e4e1dd;
  --gold:#f2b600;
}
*{box-sizing:border-box;margin:0;padding:0}
html,body{width:1200px;height:3852px;overflow:hidden}
body{font-family:"Jost",sans-serif;color:var(--ink-soft);background:var(--white);position:relative}
.heading{font-family:"Plus Jakarta Sans",sans-serif;font-weight:600;text-transform:uppercase;color:#111;letter-spacing:-1px}
.eyebrow{font-size:15px;color:var(--tan-text);font-weight:400}
.btn{display:inline-flex;align-items:center;justify-content:center;border-radius:40px;font-weight:600;text-transform:uppercase;font-size:15px;letter-spacing:.3px;white-space:nowrap}
.btn-solid{background:var(--tan);color:var(--white)}
.btn-ghost{border:2px solid var(--tan);color:var(--tan);background:var(--white)}

/* Header */
.site-header{position:absolute;top:0;left:0;width:1200px;height:88px;background:var(--ink)}
.brand{position:absolute;left:144px;top:14px;color:#d9d6d2;font-weight:300;line-height:1}
.brand-name{font-size:19px;letter-spacing:1px;display:flex;align-items:center;gap:6px;white-space:nowrap}
.brand-mark{width:14px;height:14px;border:1.5px solid #d9d6d2;flex:none}
.brand-sub{font-size:9px;letter-spacing:1.5px;margin-top:4px;text-transform:uppercase}
.top-contact{position:absolute;top:18px;left:630px;display:flex;gap:28px;color:#fff;font-size:14px;align-items:center;white-space:nowrap}
.top-contact span{display:flex;align-items:center;gap:6px}
.header-book{position:absolute;left:920px;top:12px;width:135px;height:36px;font-size:13px}
.main-nav{position:absolute;top:62px;left:363px;display:flex;gap:52px;font-size:14px;color:#fff;text-transform:uppercase;white-space:nowrap}
.main-nav .active{color:var(--tan)}

/* Hero */
.hero{position:absolute;top:88px;left:0;width:1200px;height:552px;background:linear-gradient(90deg,#e6e8e9 0%,#d8dcdc 40%,#9fb6b9 65%,#c9d6d8 100%)}
.hero-photo{position:absolute;right:0;top:0;width:560px;height:552px;background:radial-gradient(ellipse at 50% 60%,#c5d8d8 0%,#9eb9bb 45%,#7ea2a6 100%);opacity:.85}
.hero-copy{position:absolute;left:144px;top:112px}
.hero-copy h1{font-size:39px;margin-top:16px;white-space:nowrap}
.hero-copy p{font-size:18px;line-height:32px;color:#222;margin-top:14px;width:480px}
.hero-copy .btn{margin-top:38px;width:272px;height:48px;font-size:16px}
.scroll-down{position:absolute;left:0;width:1200px;top:500px;text-align:center;font-size:9px;color:#fff;letter-spacing:.5px}

/* Services */
.services{position:absolute;top:640px;left:0;width:1200px;height:550px;text-align:center}
.services .eyebrow{position:absolute;top:76px;width:100%}
.services h2{position:absolute;top:110px;width:100%;font-size:32px}
.card{position:absolute;top:187px;width:216px;height:280px;border:1px solid var(--line);background:#fff}
.card svg{margin-top:18px}
.card h3{font-weight:400;font-size:17px;color:#222;margin-top:14px}
.card p{font-size:13px;line-height:22px;color:var(--muted);margin:14px 14px 0}
.card .btn{position:absolute;left:40px;bottom:32px;width:136px;height:40px;font-size:14px}
.card.featured{background:var(--ink);border-color:var(--ink)}
.card.featured h3,.card.featured p{color:#fff}
.carousel-arrow{position:absolute;top:276px;width:44px;height:44px;border-radius:50%;background:#eef0f0;display:flex;align-items:center;justify-content:center}

/* About */
.about{position:absolute;top:1190px;left:0;width:1200px;height:494px}
.about-photo{position:absolute;left:0;top:0;width:573px;height:494px;background:linear-gradient(135deg,#cfd5dc 0%,#b9c3cc 45%,#c4825a 75%,#d9d6d2 100%)}
.about-copy{position:absolute;left:632px;top:26px;width:430px}
.about-copy h2{font-size:27px;line-height:48px;margin-top:10px;white-space:nowrap}
.body-text{font-size:13px;line-height:24px;color:var(--muted);margin-top:18px}
.body-text+.body-text{margin-top:8px}
.btn-row{display:flex;gap:16px;margin-top:28px}
.btn-row .btn{width:136px;height:40px;font-size:14px}
.btn-row .btn-ghost{width:150px}

/* Fees band */
.fees{position:absolute;top:1684px;left:0;width:1200px;height:363px;background:var(--tan-band);text-align:center;color:#fff}
.fees .eyebrow{color:#fff;position:absolute;top:60px;width:100%;font-size:14px}
.fees h2{position:absolute;top:90px;width:100%;font-size:32px;color:#fff}
.fees .lead{position:absolute;top:146px;width:100%;font-size:18px}
.fees .small{position:absolute;top:182px;left:144px;width:912px;font-size:13px;line-height:24px}
.fees .btn{position:absolute;top:263px;left:469px;width:262px;height:40px;background:#fff;color:var(--tan);font-size:14px}

/* Join */
.join{position:absolute;top:2047px;left:0;width:1200px;height:514px}
.join-copy{position:absolute;left:145px;top:66px;width:424px}
.join-copy h2{font-size:32px;margin-top:10px}
.join-photo{position:absolute;left:628px;top:0;width:572px;height:514px;background:linear-gradient(135deg,#d4d8de 0%,#b8d0d8 40%,#8fb8c6 70%,#c9ccd2 100%)}

/* Testimonials */
.reviews{position:absolute;top:2561px;left:0;width:1200px;height:536px;text-align:center}
.reviews .eyebrow{position:absolute;top:74px;width:100%}
.reviews h2{position:absolute;top:108px;width:100%;font-size:32px}
.review{position:absolute;top:186px;width:296px;height:234px;background:#fff;box-shadow:0 2px 14px rgba(0,0,0,.08);text-align:left;padding:22px 26px}
.stars{color:var(--gold);font-size:16px;letter-spacing:2px}
.quote{position:absolute;right:26px;top:18px;font-size:40px;line-height:40px;color:#ddd;font-family:Georgia,serif}
.review h3{font-weight:400;font-size:17px;color:#222;margin-top:6px}
.review p{font-size:13px;line-height:21px;color:var(--muted);margin-top:8px}
.reviewer{position:absolute;left:26px;bottom:26px;display:flex;align-items:center;gap:14px}
.avatar{width:54px;height:54px;border-radius:50%;background:linear-gradient(135deg,#d7c2b3,#9d8a7e)}
.reviewer b{display:block;font-weight:400;font-size:14px;color:#222}
.reviewer small{font-size:11px;color:#bbb}
.rating-badge{position:absolute;right:26px;bottom:38px;width:30px;height:30px;border-radius:50%;background:var(--tan)}
.dots{position:absolute;top:446px;left:0;width:100%;display:flex;justify-content:center;gap:8px}
.dots i{width:10px;height:10px;border-radius:50%;border:1px solid #777;display:block}
.dots i.on{background:#222;border-color:#222}

/* Team */
.team{position:absolute;top:3097px;left:0;width:1200px;height:418px;background:var(--light)}
.team-photo-a{position:absolute;left:0;top:67px;width:232px;height:277px;background:linear-gradient(160deg,#eef1f3 0%,#c9d3dc 50%,#6f95c2 100%)}
.team-photo-b{position:absolute;left:232px;top:67px;width:290px;height:277px;background:linear-gradient(160deg,#f0f1f2 0%,#dcdfe2 50%,#b7c0c9 100%)}
.team-arrow{position:absolute;top:191px;width:28px;height:28px;border-radius:50%;background:#fff;display:flex;align-items:center;justify-content:center}
.team-copy{position:absolute;left:603px;top:65px;width:456px}
.team-copy h2{font-size:32px;margin-top:10px}
.team-copy h3{font-weight:400;font-size:20px;color:#222;margin-top:16px}
.team-copy .btn{margin-top:28px;width:112px;height:38px;font-size:14px}

/* Footer */
.site-footer{position:absolute;top:3515px;left:0;width:1200px;height:337px;background:var(--ink);color:#fff}
.footer-brand{position:absolute;left:144px;top:74px;color:#d9d6d2;font-weight:300}
.footer-brand .brand-name{font-size:23px}
.footer-brand .brand-mark{width:18px;height:18px}
.footer-brand .brand-sub{font-size:16px;letter-spacing:1px;margin-top:6px}
.socials{position:absolute;left:164px;top:213px;display:flex;gap:8px}
.socials i{width:28px;height:28px;border-radius:50%;border:1.5px solid #fff;display:block}
.socials i.on{background:var(--tan);border-color:var(--tan)}
.footer-col{position:absolute;top:62px}
.footer-col h4{font-weight:400;font-size:19px}
.footer-col ul{list-style:none;margin-top:16px}
.footer-col li{font-size:13px;line-height:24px}
.contact-list li{display:flex;gap:10px;align-items:flex-start;line-height:18px;margin-bottom:22px}
.contact-list .ico{width:26px;height:26px;border-radius:50%;border:1.5px solid #fff;display:flex;align-items:center;justify-content:center;flex:none;margin-top:-4px}
.map{position:absolute;left:827px;top:107px;width:229px;height:138px;background:linear-gradient(135deg,#e7efe8,#d6e4d9);border-radius:2px}
.copyright{position:absolute;top:308px;width:100%;text-align:center;font-size:12px}
.chat{position:absolute;left:1069px;top:286px;width:32px;height:32px;border-radius:50%;background:var(--tan)}
</style>
</head>
<body>

<header class="site-header">
  <div class="brand">
    <div class="brand-name"><span class="brand-mark"></span>BRAMBLEFORD</div>
    <div class="brand-sub">Dental Practice</div>
  </div>
  <div class="top-contact">
    <span><svg width="12" height="12" viewBox="0 0 24 24" fill="#fff"><path d="M6.6 10.8a15 15 0 006.6 6.6l2.2-2.2c.3-.3.7-.4 1-.2 1.1.4 2.3.6 3.6.6.6 0 1 .4 1 1V20c0 .6-.4 1-1 1A17 17 0 013 4c0-.6.4-1 1-1h3.5c.6 0 1 .4 1 1 0 1.3.2 2.5.6 3.6.1.3 0 .7-.2 1z"/></svg>1-800-555-0142</span>
    <span><svg width="13" height="11" viewBox="0 0 24 18" fill="none" stroke="#fff" stroke-width="2"><rect x="1" y="1" width="22" height="16" rx="2"/><path d="M1 2l11 8 11-8"/></svg>care@bfdental.com</span>
  </div>
  <span class="btn btn-solid header-book">Book Online</span>
  <nav class="main-nav">
    <span class="active">Home</span><span>About Us</span><span>New Patients</span><span>Treatments</span><span>Fees</span><span>Contact Us</span>
  </nav>
</header>

<section class="hero">
  <div class="hero-photo" role="img" aria-label="Smiling patient in a dental chair with a dentist and nurse in masks"></div>
  <div class="hero-copy">
    <div class="eyebrow">Welcome To</div>
    <h1 class="heading">Brambleford Dental Practice</h1>
    <p>We’re Confident That We Can Deliver The Highest Quality Treatment To You And Your Loved Ones.</p>
    <span class="btn btn-solid">Book An Appointment &nbsp;›</span>
  </div>
  <div class="scroll-down">SCROLL DOWN<br>⌄</div>
</section>

<section class="services">
  <div class="eyebrow">Our Services</div>
  <h2 class="heading">Dental Treatments</h2>
  <div class="carousel-arrow" style="left:80px"><svg width="18" height="10" viewBox="0 0 18 10" fill="none" stroke="#333" stroke-width="1.5"><path d="M17 5H2M6 1L2 5l4 4"/></svg></div>
  <div class="carousel-arrow" style="left:1075px"><svg width="18" height="10" viewBox="0 0 18 10" fill="none" stroke="#333" stroke-width="1.5"><path d="M1 5h15M12 1l4 4-4 4"/></svg></div>

  <div class="card" style="left:144px">
    <svg width="70" height="52" viewBox="0 0 70 52" fill="none" stroke="#9a8b7c" stroke-width="1.6"><path d="M6 6c6-4 12 0 14 4 2-4 8-8 14-4 5 4 2 16 0 22-2 8-4 18-7 18-3 0-3-12-7-12s-4 12-7 12c-3 0-5-10-7-18C4 22 1 10 6 6z"/><path d="M36 6c6-4 12 0 14 4 2-4 8-8 14-4 5 4 2 16 0 22-2 8-4 18-7 18-3 0-3-12-7-12s-4 12-7 12"/><path d="M2 26h66"/></svg>
    <h3>Teeth Straightening</h3>
    <p>Lorem ipsum dolor sit amet, consectetur adipiscing elit, sed do eiusmod tempor</p>
    <span class="btn btn-solid">Read More</span>
  </div>
  <div class="card" style="left:376px">
    <svg width="40" height="58" viewBox="0 0 40 58" fill="none" stroke="#9a8b7c" stroke-width="1.6"><path d="M6 4c5-3 10 0 14 2 4-2 9-5 14-2 4 4 1 12-2 16H8C5 16 2 8 6 4z"/><path d="M8 22h24M12 28h16M13 34h14M14 40h12M15 46h10M17 52l3 4 3-4"/></svg>
    <h3>Dental Implants</h3>
    <p>Lorem ipsum dolor sit amet, consectetur adipiscing elit, sed do eiusmod tempor</p>
    <span class="btn btn-solid">Read More</span>
  </div>
  <div class="card featured" style="left:607px">
    <svg width="50" height="56" viewBox="0 0 50 56" fill="none" stroke="#a8998a" stroke-width="1.8"><path d="M8 4c7-4 13 0 17 3 4-3 10-7 17-3 7 5 3 19 1 26-2 10-5 24-9 24s-4-16-9-16-5 16-9 16-7-14-9-24C5 23 1 9 8 4z"/><path d="M12 9c3-1 6 0 8 2"/></svg>
    <h3>General Dentistry</h3>
    <p>Lorem ipsum dolor sit amet, consectetur adipiscing elit, sed do eiusmod tempor</p>
    <span class="btn btn-solid">Read More</span>
  </div>
  <div class="card" style="left:839px">
    <svg width="58" height="56" viewBox="0 0 58 56" fill="none" stroke="#9a8b7c" stroke-width="1.6"><path d="M14 10c6-4 11 0 15 3 4-3 9-7 15-3 6 5 2 17 0 23-2 9-4 20-8 20s-4-14-7-14-4 14-8 14-6-11-8-20C12 27 8 15 14 10z"/><path d="M6 2l1.5 4 4 1.5-4 1.5L6 13l-1.5-4-4-1.5 4-1.5zM52 40l1.2 3 3 1.2-3 1.2-1.2 3-1.2-3-3-1.2 3-1.2z"/></svg>
    <h3>Cosmetic Dentistry</h3>
    <p>Lorem ipsum dolor sit amet, consectetur adipiscing elit, sed do eiusmod tempor</p>
    <span class="btn btn-solid">Read More</span>
  </div>
</section>

<section class="about">
  <div class="about-photo" role="img" aria-label="Dentist treating a patient in an orange dental chair in a bright surgery room"></div>
  <div class="about-copy">
    <div class="eyebrow">About Us</div>
    <h2 class="heading">Introduction Brambleford<br>Dental Practice</h2>
    <p class="body-text">Welcome to our friendly dental practice nestled in the heart of beautiful Ashcombe, UK. Our team of dedicated dentists, hygienists and support staff are here to provide you with exceptional dental care.</p>
    <p class="body-text">With a wide array of services, including general and cosmetic dentistry, orthodontics and emergency care, we’re confident that we can deliver the highest quality treatment to you and your loved ones.At our practice, we believe that a visit to the dentist should be a comfortable and positive experience.</p>
    <div class="btn-row"><span class="btn btn-solid">Learn More</span><span class="btn btn-ghost">Book Online</span></div>
  </div>
</section>

<section class="fees">
  <div class="eyebrow">Fees</div>
  <h2 class="heading">Maintenance Plans &amp; Finance Options</h2>
  <p class="lead">Lorem ipsum dolor sit amet, consectetur adipiscing elit, sed do eiusmod tempor incididunt ut labore</p>
  <p class="small">Sed ut perspiciatis unde omnis iste natus error sit voluptatem accusantium doloremque laudantium, totam rem aperiam, eaque ipsa quae ab illo inventore veritatis et quasi architecto beatae vitae dicta sunt explicabo nisi ut aliquip ex ea commodo consequat.</p>
  <span class="btn">View Maintenance Plans</span>
</section>

<section class="join">
  <div class="join-copy">
    <div class="eyebrow">Join</div>
    <h2 class="heading">Our Practice</h2>
    <p class="body-text">If you’re looking for an exceptional dental practice, we’re here to help! Our team is made up of highly skilled professionals who are dedicated to ensuring that all our patients receive top-notch care in a welcoming and comfortable environment.</p>
    <p class="body-text">Whether you need a routine examination or a more specialised treatment, we have all the resources to provide you with the best dental care possible. Our practice is always up-to-date with the latest techniques and technologies to make sure that our patients receive the best possible results.</p>
    <div class="btn-row"><span class="btn btn-solid">Join Now</span><span class="btn btn-ghost">Book Online</span></div>
  </div>
  <div class="join-photo" role="img" aria-label="Dental nurse examining a smiling patient in a light blue treatment room"></div>
</section>

<section class="reviews">
  <div class="eyebrow">Reviews</div>
  <h2 class="heading">Customer Testimonials</h2>
  <div class="review" style="left:142px">
    <div class="stars">★★★★★</div><span class="quote">”</span>
    <h3>Highly Recommend</h3>
    <p>Sed ut perspiciatis unde omnis iste natus error sit voluptatem accusantium dolore mque laudantium, totam aperiam,</p>
    <div class="reviewer"><span class="avatar" role="img" aria-label="Reviewer portrait"></span><span><b>Mara Penhale</b><small>24/10/2021</small></span></div>
    <span class="rating-badge" role="img" aria-label="Ravelle ratings badge"></span>
  </div>
  <div class="review" style="left:451px">
    <div class="stars">★★★★★</div><span class="quote">”</span>
    <h3>Highly Recommend</h3>
    <p>Sed ut perspiciatis unde omnis iste natus error sit voluptatem accusantium dolore mque laudantium, totam aperiam,</p>
    <div class="reviewer"><span class="avatar" role="img" aria-label="Reviewer portrait"></span><span><b>Lena Whitcombe</b><small>24/10/2021</small></span></div>
    <span class="rating-badge" role="img" aria-label="Ravelle ratings badge"></span>
  </div>
  <div class="review" style="left:759px">
    <div class="stars">★★★★★</div><span class="quote">”</span>
    <h3>Highly Recommend</h3>
    <p>Sed ut perspiciatis unde omnis iste natus error sit voluptatem accusantium dolore mque laudantium, totam aperiam,</p>
    <div class="reviewer"><span class="avatar" role="img" aria-label="Reviewer portrait"></span><span><b>Owen Carrow</b><small>24/10/2021</small></span></div>
    <span class="rating-badge" role="img" aria-label="Ravelle ratings badge"></span>
  </div>
  <div class="dots"><i></i><i class="on"></i><i></i><i></i></div>
</section>

<section class="team">
  <div class="team-photo-a" role="img" aria-label="Smiling dentist in blue scrubs"></div>
  <div class="team-photo-b" role="img" aria-label="Smiling dentist in a white coat"></div>
  <span class="team-arrow" style="left:217px"><svg width="12" height="8" viewBox="0 0 12 8" fill="none" stroke="#333" stroke-width="1.3"><path d="M11 4H1M4 1L1 4l3 3"/></svg></span>
  <span class="team-arrow" style="left:508px"><svg width="12" height="8" viewBox="0 0 12 8" fill="none" stroke="#333" stroke-width="1.3"><path d="M1 4h10M8 1l3 3-3 3"/></svg></span>
  <div class="team-copy">
    <div class="eyebrow">Dentist</div>
    <h2 class="heading">Meet The Team</h2>
    <h3>Dr. Elias Marlow</h3>
    <p class="body-text">Sed ut perspiciatis unde omnis iste natus error sit voluptatem accusantium doloremque laudantium, totam rem aperiam, eaque ipsa quae ab illo inventore veritatis et quasi architecto beatae vitae</p>
    <span class="btn btn-solid">View Bio</span>
  </div>
</section>

<footer class="site-footer">
  <div class="footer-brand">
    <div class="brand-name"><span class="brand-mark"></span>BRAMBLEFORD</div>
    <div class="brand-sub">DENTAL PRACTICE</div>
  </div>
  <div class="socials"><i></i><i class="on"></i><i></i></div>
  <div class="footer-col" style="left:375px">
    <h4>Quick Links</h4>
    <ul><li>Pool Services</li><li>Galleries</li><li>Resources</li><li>Our Company</li><li>Contact</li></ul>
  </div>
  <div class="footer-col" style="left:565px">
    <h4>Contact Details</h4>
    <ul class="contact-list">
      <li><span class="ico"><svg width="11" height="11" viewBox="0 0 24 24" fill="#fff"><path d="M6.6 10.8a15 15 0 006.6 6.6l2.2-2.2c.3-.3.7-.4 1-.2 1.1.4 2.3.6 3.6.6.6 0 1 .4 1 1V20c0 .6-.4 1-1 1A17 17 0 013 4c0-.6.4-1 1-1h3.5c.6 0 1 .4 1 1 0 1.3.2 2.5.6 3.6.1.3 0 .7-.2 1z"/></svg></span>+1-800-555-0142</li>
      <li><span class="ico"><svg width="12" height="9" viewBox="0 0 24 18" fill="none" stroke="#fff" stroke-width="2.4"><rect x="1" y="1" width="22" height="16" rx="2"/><path d="M1 2l11 8 11-8"/></svg></span>care@bfdental.com</li>
      <li><span class="ico"><svg width="10" height="13" viewBox="0 0 20 26" fill="none" stroke="#fff" stroke-width="2.4"><path d="M10 25s8-9 8-15a8 8 0 00-16 0c0 6 8 15 8 15z"/><circle cx="10" cy="10" r="3"/></svg></span>12 Willow Lane,<br>Ashcombe AB1 2CD</li>
      <li><span class="ico"><svg width="10" height="13" viewBox="0 0 20 26" fill="none" stroke="#fff" stroke-width="2.4"><path d="M10 25s8-9 8-15a8 8 0 00-16 0c0 6 8 15 8 15z"/><circle cx="10" cy="10" r="3"/></svg></span>Mon -Sat: 8AM To 9PM</li>
    </ul>
  </div>
  <div class="footer-col" style="left:825px"><h4>Visit Us</h4></div>
  <div class="map" role="img" aria-label="Map showing the practice location"></div>
  <span class="chat"></span>
  <div class="copyright">© 2025 Copyright All Right Reserved. Brambleford Dental Practice</div>
</footer>

</body>
</html>
```